Tavenhurst Falcons FC Website

We are looking to develop a new website for Tavenhurst FC. Tavenhurst FC has now joined with Tavenhurst Falcons FC and we are looking at a website that can work for both clubs. Tavenhurst FC play in a local park football competition while tavenhurst Falcons are a Semi Professional team that plays in the Ostral Premier Series Competition. What we are after is two separate website off the one platform. I have attached both team logos for you to visualise. Also you can look at the existing tavenhurst website www.tavenhurstfc.net.au. We are looking for a huge improvement in the website and it will be imperative we have links to sponsors and the sponsors can get regular visuals. Weare looking to move this club forward and have a very professional website that can communicate clearly with the community.

Hi All,

Please remember that the website is to represent two clubs;
1. Tavenhurst Falcons FC (Competes in Semi Professional League)
2. Tavenhurst FC (Compete in KPWLT League which is a lower level)

Further to this the Tavenhurst Falcons FC page will require a player profile page which will show photos of each player and a little bio on each.

Thanks

Reason: Would like to spend more time review existing and new designs

```html
<!DOCTYPE html>
<html lang="en">
<head>
<meta charset="utf-8">
<title>Tavenhurst Falcons FC</title>
<link href="https://fonts.googleapis.com/css2?family=Arimo:wght@400;700&display=swap" rel="stylesheet">
<style>
:root{
  --green:#3f9a2b;
  --green-light:#48a532;
  --green-dark:#2f7f20;
  --footer:#317d22;
  --red:#d9121b;
  --red-dark:#b50d14;
  --white:#ffffff;
  --text:#ffffff;
  --muted:#e6f2e0;
  --line:rgba(255,255,255,.35);
  --nav-text:#555;
}
*{box-sizing:border-box;margin:0;padding:0}
html,body{width:840px;height:1200px;overflow:hidden}
body{
  font-family:"Arimo",Arial,sans-serif;color:var(--text);position:relative;
  background:repeating-linear-gradient(90deg,var(--green) 0 26px,var(--green-light) 26px 52px);
}
.abs{position:absolute}
a{color:inherit}
/* header */
.crest{left:88px;top:13px;width:84px;height:84px;border-radius:50%;background:var(--red);border:4px solid var(--white)}
.site-title{left:190px;top:35px;font-size:20px;font-weight:700}
.site-tag{left:190px;top:58px;font-size:12px}
.register{left:644px;top:35px;width:109px;height:24px;background:var(--red);border:2px solid var(--red-dark);outline:1px solid #f06;font-size:9.5px;display:flex;align-items:center;justify-content:center;letter-spacing:.2px}
.toplinks{right:86px;top:88px;display:flex;align-items:center;gap:19px;font-size:8.8px}
/* nav */
.mainnav{left:86px;top:113px;width:668px;height:33px;background:var(--white);padding:4px;display:flex}
.mainnav span{flex:auto;display:flex;align-items:center;justify-content:center;font-size:9.3px;color:var(--nav-text);border-right:1px solid #ddd;background:linear-gradient(#fff,#f1f1f1)}
.mainnav span:last-child{border-right:0}
.mainnav .active{background:var(--red);color:var(--white);flex:0 0 79px}
/* slider */
.slider{left:86px;top:167px;width:668px;height:315px;background:var(--white);padding:7px;box-shadow:0 2px 6px rgba(0,0,0,.25)}
.slide{width:100%;height:100%;background:linear-gradient(90deg,#6e6456,#9b8d7b 35%,#4d4640 70%,#7a6f63)}
.dots{left:644px;top:457px;display:flex;gap:4px}
.dots i{width:9px;height:9px;border-radius:50%;background:var(--white)}
.dots i:first-child{background:var(--red)}
/* welcome */
h2{font-weight:400;font-size:17.5px}
h2 b{font-weight:700}
.welcome{left:86px;top:509px;width:403px}
.welcome h2{padding-bottom:7px;border-bottom:1px solid var(--line)}
.welcome ul{list-style:none;margin-top:10px;font-size:8.6px;line-height:10.5px;color:var(--muted)}
.welcome li{padding-left:10px;position:relative;margin-bottom:9px}
.welcome li:before{content:"";position:absolute;left:1px;top:4px;width:4px;height:4px;border-radius:50%;background:var(--white)}
.btn{background:var(--white);color:var(--red);font-size:8.8px;display:flex;align-items:center;justify-content:center;height:16px}
.member{left:523px;top:511px;width:231px;height:179px;background:radial-gradient(circle at 35% 60%,#c4141c,#e11d26 70%)}
.member .seal{position:absolute;left:22px;top:40px;width:100px;height:100px;border-radius:50%;background:rgba(150,10,15,.45)}
.member .head{position:absolute;right:17px;top:30px;text-align:right;font-size:16.5px;line-height:19px}
.member .year{position:absolute;right:17px;top:72px;font-size:26px;font-weight:700}
.member .join{position:absolute;left:146px;top:121px;width:68px;height:20px;font-weight:700;font-size:8.8px}
/* news */
.topnews{left:86px;top:714px;width:403px}
.arrows{left:469px;top:718px}
.news{left:87px;width:403px;display:flex;gap:13px}
.thumb{width:73px;height:74px;border:3px solid var(--white);flex:none}
.news h3{font-size:8.6px;line-height:10.5px;font-weight:700;margin-top:3px}
.news p{font-size:8.6px;line-height:10.5px;color:var(--muted);margin-top:9px}
.more{display:flex;align-items:center;gap:6px;margin-top:11px;font-size:8.8px}
.more a{text-decoration:underline}
/* fixtures */
.fixtures{left:523px;top:714px;width:231px}
.tabs{left:523px;top:741px;width:231px;display:grid;grid-template-columns:86px 78px 67px;border:1px solid var(--line)}
.tabs span{height:23px;display:flex;align-items:center;padding-left:7px;font-size:8.8px;font-weight:700;border-right:1px solid var(--line);border-bottom:1px solid var(--line)}
.tabs .on{background:var(--red)}
.table{left:523px;top:787px;width:231px;height:122px;border:1px dashed var(--line);display:grid;grid-template-columns:1fr 1fr}
.col{border-right:1px dashed var(--line)}
.col:last-child{border-right:0}
.col h4{font-weight:400;font-size:8.8px;height:23px;display:flex;align-items:center;padding-left:13px;background:var(--green-dark);border-bottom:1px solid var(--line)}
.col ul{list-style:none;font-size:8.4px;line-height:14.4px;padding:12px 0 0 13px}
.col li:before{content:"»";margin-right:5px}
/* footer */
.footer{left:0;top:1000px;width:840px;height:114px;background:var(--footer);border-bottom:1px solid rgba(255,255,255,.15)}
.fcol{top:1020px;font-size:8.6px;line-height:10.5px}
.fcol h5{font-size:8.8px;font-weight:700;margin-bottom:9px}
.fcol ul{list-style:none}
.fcol li:before{content:"• "}
.sponsor{top:1041px;width:82px;height:39px;background:var(--white);color:#444;font-size:8.6px;font-weight:700;display:flex;align-items:center;justify-content:center;text-align:center}
.viewall-f{left:704px;top:1017px;display:flex;align-items:center;gap:6px;font-size:8.8px}
.copy{left:0;width:840px;top:1131px;text-align:center;font-size:8.6px;line-height:11px}
.copy a{color:#ffd5c8}
.social{left:384px;top:1164px;display:flex;gap:7px}
.social i{width:20px;height:20px;border-radius:50%;background:var(--white);border:2px solid var(--red)}
</style>
</head>
<body>
<div class="abs crest" role="img" aria-label="Club crest"></div>
<div class="abs site-title">Tavenhurst Falcons FC</div>
<div class="abs site-tag">The Official Website of Tavenhurst Falcons FC</div>
<div class="abs register">REGISTER ONLINE</div>
<nav class="abs toplinks">
  <svg width="17" height="15" viewBox="0 0 17 15"><path d="M1 8 8.5 1 16 8" fill="none" stroke="#fff" stroke-width="2"/><path d="M3.5 7.5V14h4v-4h2v4h4V7.5" fill="#fff"/></svg>
  <span>About Us</span><span>Media</span><span>Contact Us</span>
</nav>
<nav class="abs mainnav">
  <span class="active">LATEST NEWS</span><span>FIXTURE &amp; RESULTS</span><span>HISTORY</span><span>PROFILE</span><span>MANAGEMENT</span><span>SQUAD</span><span>MEMBERSHIP</span><span>GALLERY</span><span>VIDEO</span><span>SPONSORS</span>
</nav>
<div class="abs slider"><div class="slide" role="img" aria-label="Club officials holding trophies at an awards night"></div></div>
<div class="abs dots"><i></i><i></i><i></i><i></i><i></i><i></i></div>

<section class="abs welcome">
  <h2>Welcome to <b>Tavenhurst Falcons FC</b></h2>
  <ul>
    <li>Lorem ipsum dolor sit amet, consectetur adipisicing elit, sed do eiusmod tempor incididunt ut labore et dolore magna aliqua.</li>
    <li>Lorem ipsum dolor sit amet, consectetur adipisicing elit.</li>
    <li>Lorem ipsum dolor sit amet, consectetur adipisicing elit, sed do eiusmod tempor incididunt ut labore et dolore magna aliqua.</li>
    <li>Lorem ipsum dolor sit amet, consectetur adipisicing elit, sed do eiusmod tempor incididunt ut labore et dolore magna aliqua. Ut enim ad minim veniam, quis nostrud exercitation ullamco laboris nisi ut aliquip ex ea commodo consequat.</li>
  </ul>
</section>
<div class="abs btn" style="left:86px;top:676px;width:55px">Read More</div>

<aside class="abs member">
  <div class="seal" role="img" aria-label="Club shirt with embroidered badge"></div>
  <div class="head">BECOME<br>A MEMBER</div>
  <div class="year">2014</div>
  <div class="btn join">JOIN NOW</div>
</aside>

<h2 class="abs topnews">Top <b>News</b></h2>
<svg class="abs arrows" width="20" height="14" viewBox="0 0 20 14"><path d="M6 2 2 7l4 5" fill="none" stroke="#cfe6c6" stroke-width="2"/><path d="M13 2l4 5-4 5" fill="none" stroke="#fff" stroke-width="2"/></svg>

<article class="abs news" style="top:755px">
  <div class="thumb" role="img" aria-label="Coach on the sideline" style="background:linear-gradient(#6f9cc8,#5c8a3e)"></div>
  <div>
    <h3>Lorem ipsum dolor sit amet, consectetur adipisicing elit, sed do eiusmod tempor incididunt ut labore et dolore magna aliqua.</h3>
    <p>Lorem Ipsum is simply dummy text of the printing and typesetting industry. Lorem Ipsum has been the industry's standard dummy text ever since the 1500s....</p>
    <div class="more"><svg width="14" height="14" viewBox="0 0 14 14"><circle cx="7" cy="7" r="7" fill="#fff"/><path d="M6 4l3 3-3 3" fill="none" stroke="#d9121b" stroke-width="2"/></svg><a>Read More</a></div>
  </div>
</article>
<article class="abs news" style="top:858px">
  <div class="thumb" role="img" aria-label="Junior players during a match" style="background:linear-gradient(#b9c7a8,#5f9440)"></div>
  <div>
    <h3>Lorem ipsum dolor sit amet, consectetur adipisicing elit, sed do eiusmod tempor incididunt ut labore et dolore magna aliqua.</h3>
    <p>Lorem Ipsum is simply dummy text of the printing and typesetting industry. Lorem Ipsum has been the industry's standard dummy text ever since the 1500s....</p>
    <div class="more"><svg width="14" height="14" viewBox="0 0 14 14"><circle cx="7" cy="7" r="7" fill="#fff"/><path d="M6 4l3 3-3 3" fill="none" stroke="#d9121b" stroke-width="2"/></svg><a>Read More</a></div>
  </div>
</article>
<div class="abs btn" style="left:86px;top:954px;width:55px">View All</div>

<h2 class="abs fixtures">Fixtures &amp; <b>Results</b></h2>
<div class="abs tabs">
  <span class="on">Premier League</span><span>Super League</span><span>Under 16 / 2</span><span>Under 17 / 1</span>
</div>
<div class="abs table">
  <div class="col"><h4>FIXTURES</h4><ul><li>Under 10 / 2</li><li>AA Men / 5</li><li>07 ECL / Red</li><li>06 / A Green</li></ul></div>
  <div class="col"><h4>RESULTS</h4><ul><li>Under 10 / 3</li><li>AA Men / 6</li><li>07 ECL / Green</li><li>06 / B Blue</li></ul></div>
</div>
<div class="abs btn" style="left:523px;top:928px;width:55px">View All</div>

<footer class="abs footer"></footer>
<div class="abs fcol" style="left:86px"><h5>HOME</h5><ul><li><a style="text-decoration:underline">News</a></li><li>Gallery</li><li>Sponsor</li><li>Contact Us</li></ul></div>
<div class="abs fcol" style="left:187px"><h5>PROFILE</h5><ul><li>Management</li><li>History</li><li>Coach History</li><li>Awards</li></ul></div>
<div class="abs fcol" style="left:306px"><h5>SPONSOR'S</h5></div>
<div class="abs viewall-f"><svg width="14" height="14" viewBox="0 0 14 14"><circle cx="7" cy="7" r="7" fill="#fff"/><path d="M6 4l3 3-3 3" fill="none" stroke="#d9121b" stroke-width="2"/></svg><a style="text-decoration:underline">View All</a></div>
<div class="abs sponsor" style="left:306px">Brightpath Media</div>
<div class="abs sponsor" style="left:398px">Harlow &amp; Co</div>
<div class="abs sponsor" style="left:489px">Northgate</div>
<div class="abs sponsor" style="left:580px">Eastfield Trophies</div>
<div class="abs sponsor" style="left:671px">Veldmark</div>

<div class="abs copy">Copyright © 2014. All Rights Reserved.<br><a style="text-decoration:underline">Privacy Policy</a></div>
<div class="abs social" aria-label="Social links"><i></i><i></i><i></i></div>
</body>
</html>
```